Visitenkarten-Design für Boutique-Unternehmensberatung
Zielgruppe
Boutique Unternehmensberatung für die Chemische Industrie. Wir unterstützen Unternehmen, die Beziehung zu Ihren Händlern zu optimieren.
Vorläufige Website vertriebsbruecke-online.de kann ggf weitere Einblicke geben. Hinweis: Diese Website wurde bisher noch nicht professionell erstellt.
Aufgabenstellung
Die Visitenkarte sollte vertrauenserweckend und seriös wirken. Zeitgleich aber auch modern.

```html
<!DOCTYPE html>
<html lang="de">
<head>
<meta charset="utf-8">
<title>Visitenkarten – Vertriebsbrücke</title>
<link rel="stylesheet" href="https://fonts.googleapis.com/css2?family=Montserrat:wght@500;600;700&display=swap">
<style>
  :root {
    --brand-blue: #16568f;
    --paper: #ffffff;
    --canvas: #ffffff;
    --photo-light: #c9b3a4;
    --photo-dark: #6f7f8c;
    --shadow: rgba(0,0,0,.38);
  }
  * { box-sizing: border-box; margin: 0; padding: 0; }
  html, body { width: 1200px; height: 940px; overflow: hidden; background: var(--canvas); }
  body { position: relative; font-family: "Montserrat", Arial, sans-serif; }

  .card {
    position: absolute; width: 257px; height: 166px;
    box-shadow: 4px 6px 7px var(--shadow); overflow: hidden;
  }
  .card--front { left: 338px; background: var(--brand-blue); }
  .card--front.card--light { background: var(--paper); }
  .card--back { left: 616px; background: var(--paper); }
  .card--back.card--dark-base { background: var(--brand-blue); }

  .row-1 { top: 89px; } .row-2 { top: 285px; } .row-3 { top: 483px; } .row-4 { top: 679px; }

  .wordmark {
    position: absolute; display: flex; flex-direction: column; align-items: center;
    color: var(--paper); font-weight: 700; letter-spacing: -.2px;
  }
  .card--front .wordmark { left: 0; right: 0; top: 46px; font-size: 17px; gap: 10px; }
  .card--front.card--light .wordmark { color: var(--brand-blue); }
  .wordmark__dot { width: 34px; height: 34px; border-radius: 50%; background: currentColor; }
  .card--back .wordmark { right: 12px; bottom: 12px; width: 70px; font-size: 9px; gap: 5px; color: var(--brand-blue); }
  .card--back .wordmark .wordmark__dot { width: 20px; height: 20px; }
  .card--dark-base .wordmark { color: var(--paper); }

  .wave { position: absolute; inset: 0; width: 257px; height: 166px; }
  .wave path { fill: var(--brand-blue); }
  .card--dark-base .wave path { fill: var(--paper); }

  .bar { position: absolute; left: 0; bottom: 0; width: 117px; height: 6px; background: var(--brand-blue); }

  .person { position: absolute; left: 14px; top: 12px; color: var(--paper); }
  .card--dark-base .person { color: var(--brand-blue); }
  .person__name { font-size: 14px; font-weight: 700; line-height: 16px; }
  .person__role { font-size: 8px; font-weight: 500; line-height: 10px; margin-bottom: 6px; }

  .company { position: absolute; left: 14px; top: 98px; color: var(--brand-blue); }
  .card--dark-base .company { color: var(--paper); }
  .company__name { font-size: 6px; font-weight: 700; line-height: 8px; }
  .company__address { font-size: 6px; font-weight: 500; line-height: 9px; margin-bottom: 7px; }

  .contact { list-style: none; }
  .contact li { display: flex; align-items: center; gap: 4px; font-size: 6px; font-weight: 600; line-height: 10.5px; }
  .contact svg { width: 7px; height: 7px; flex: none; }
  .contact .icon-bg { fill: currentColor; }
  .contact .icon-fg { fill: var(--brand-blue); }
  .card--top-blue .company .icon-fg { fill: var(--paper); }
  .card--dark-base .person .icon-fg { fill: var(--paper); }

  .photo {
    position: absolute; left: 161px; top: 16px; width: 60px; height: 60px; border-radius: 50%;
    border: 3px solid var(--paper);
    background: radial-gradient(circle at 50% 42%, var(--photo-light) 0 38%, var(--photo-dark) 72%);
  }
  .card--dark-base .photo { top: 20px; border-color: var(--brand-blue); box-shadow: 0 0 0 1px var(--paper); }
</style>
</head>
<body>
<svg width="0" height="0" style="position:absolute" aria-hidden="true">
  <symbol id="icon-phone" viewBox="0 0 10 10">
    <circle class="icon-bg" cx="5" cy="5" r="5"/>
    <path class="icon-fg" d="M3 2.4l1.1-.2.6 1.5-.7.6c.3.7.8 1.2 1.5 1.5l.6-.7 1.5.6-.2 1.1C5.2 7.2 2.8 4.8 3 2.4z"/>
  </symbol>
  <symbol id="icon-mail" viewBox="0 0 10 10">
    <circle class="icon-bg" cx="5" cy="5" r="5"/>
    <path class="icon-fg" d="M2.6 3.3h4.8v3.4H2.6zM2.9 3.6L5 5.2l2.1-1.6" />
  </symbol>
  <symbol id="icon-web" viewBox="0 0 10 10">
    <circle class="icon-bg" cx="5" cy="5" r="5"/>
    <circle class="icon-fg" cx="5" cy="5" r="2.4"/>
  </symbol>
</svg>

<!-- Row 1 -->
<section class="card card--front row-1">
  <div class="wordmark"><span class="wordmark__dot"></span>Vertriebsbrücke</div>
</section>
<section class="card card--back card--top-blue row-1">
  <svg class="wave" viewBox="0 0 257 166"><path d="M0 0H257V38C205 62 120 78 0 82Z"/></svg>
  <div class="person">
    <p class="person__name">Jonas Kellner</p>
    <p class="person__role">Geschäftsführer / CEO</p>
    <ul class="contact">
      <li><svg><use href="#icon-phone"/></svg>+49 6151 / 12 34 56 78</li>
      <li><svg><use href="#icon-mail"/></svg>jk@vertriebsbruecke-online.de</li>
    </ul>
  </div>
  <div class="photo" role="img" aria-label="Porträtfoto des Geschäftsführers"></div>
  <div class="company">
    <p class="company__name">JKB Vertriebsbrücke GmbH i.G.</p>
    <p class="company__address">Lindenweg 4 · 64283 Darmstadt</p>
    <ul class="contact">
      <li><svg><use href="#icon-phone"/></svg>+49 6151 / 12 34 56 78</li>
      <li><svg><use href="#icon-mail"/></svg>info@vertriebsbruecke-online.de</li>
      <li><svg><use href="#icon-web"/></svg>www.vertriebsbruecke-online.de</li>
    </ul>
  </div>
  <div class="wordmark"><span class="wordmark__dot"></span>Vertriebsbrücke</div>
</section>

<!-- Row 2 -->
<section class="card card--front row-2">
  <div class="wordmark"><span class="wordmark__dot"></span>Vertriebsbrücke</div>
</section>
<section class="card card--back card--top-blue row-2">
  <svg class="wave" viewBox="0 0 257 166"><path d="M0 0H257V38C205 62 120 78 0 82Z"/></svg>
  <div class="person">
    <p class="person__name">Jonas Kellner</p>
    <p class="person__role">Geschäftsführer / CEO</p>
    <ul class="contact">
      <li><svg><use href="#icon-phone"/></svg>+49 6151 / 12 34 56 78</li>
      <li><svg><use href="#icon-mail"/></svg>jk@vertriebsbruecke-online.de</li>
    </ul>
  </div>
  <div class="photo" role="img" aria-label="Porträtfoto des Geschäftsführers"></div>
  <div class="company">
    <p class="company__name">JKB Vertriebsbrücke GmbH i.G.</p>
    <p class="company__address">Lindenweg 4 · 64283 Darmstadt</p>
    <ul class="contact">
      <li><svg><use href="#icon-phone"/></svg>+49 6151 / 12 34 56 78</li>
      <li><svg><use href="#icon-mail"/></svg>info@vertriebsbruecke-online.de</li>
      <li><svg><use href="#icon-web"/></svg>www.vertriebsbruecke-online.de</li>
    </ul>
  </div>
  <div class="wordmark"><span class="wordmark__dot"></span>Vertriebsbrücke</div>
  <div class="bar"></div>
</section>

<!-- Row 3 -->
<section class="card card--front card--light row-3">
  <div class="wordmark"><span class="wordmark__dot"></span>Vertriebsbrücke</div>
</section>
<section class="card card--back card--dark-base row-3">
  <svg class="wave" viewBox="0 0 257 166"><path d="M0 0H257V22C205 58 120 74 0 80Z"/></svg>
  <div class="person">
    <p class="person__name">Jonas Kellner</p>
    <p class="person__role">Geschäftsführer / CEO</p>
    <ul class="contact">
      <li><svg><use href="#icon-phone"/></svg>+49 6151 / 12 34 56 78</li>
      <li><svg><use href="#icon-mail"/></svg>jk@vertriebsbruecke-online.de</li>
    </ul>
  </div>
  <div class="photo" role="img" aria-label="Porträtfoto des Geschäftsführers"></div>
  <div class="company">
    <p class="company__name">JKB Vertriebsbrücke GmbH i.G.</p>
    <p class="company__address">Lindenweg 4 · 64283 Darmstadt</p>
    <ul class="contact">
      <li><svg><use href="#icon-phone"/></svg>+49 6151 / 12 34 56 78</li>
      <li><svg><use href="#icon-mail"/></svg>info@vertriebsbruecke-online.de</li>
      <li><svg><use href="#icon-web"/></svg>www.vertriebsbruecke-online.de</li>
    </ul>
  </div>
  <div class="wordmark"><span class="wordmark__dot"></span>Vertriebsbrücke</div>
</section>

<!-- Row 4 -->
<section class="card card--front row-4">
  <div class="wordmark"><span class="wordmark__dot"></span>Vertriebsbrücke</div>
</section>
<section class="card card--back card--dark-base row-4">
  <svg class="wave" viewBox="0 0 257 166"><path d="M0 0H257V22C205 58 120 74 0 80Z"/></svg>
  <div class="person">
    <p class="person__name">Jonas Kellner</p>
    <p class="person__role">Geschäftsführer / CEO</p>
    <ul class="contact">
      <li><svg><use href="#icon-phone"/></svg>+49 6151 / 12 34 56 78</li>
      <li><svg><use href="#icon-mail"/></svg>jk@vertriebsbruecke-online.de</li>
    </ul>
  </div>
  <div class="photo" role="img" aria-label="Porträtfoto des Geschäftsführers"></div>
  <div class="company">
    <p class="company__name">JKB Vertriebsbrücke GmbH i.G.</p>
    <p class="company__address">Lindenweg 4 · 64283 Darmstadt</p>
    <ul class="contact">
      <li><svg><use href="#icon-phone"/></svg>+49 6151 / 12 34 56 78</li>
      <li><svg><use href="#icon-mail"/></svg>info@vertriebsbruecke-online.de</li>
      <li><svg><use href="#icon-web"/></svg>www.vertriebsbruecke-online.de</li>
    </ul>
  </div>
  <div class="wordmark"><span class="wordmark__dot"></span>Vertriebsbrücke</div>
</section>
</body>
</html>
```